Brisk Fixwell business card

I need business card for my business, I think you have all my details.six months ago I design with you car wrap design. We would like to design both side of the card. On front of card we would like logo , Name and our contact details.
At the back we are looking to mentioned our services.
The name will be:
Faridoullan Mestor
Managing Director
Ph:07952338417
Email:info@brisk-fixwell.com
Web:www.brisk-fixwell.com
So we have our logo, you don’t need to change the logo.
Please see the attachment.
Thanks

Target Market(s)

Home improvement

Industry/Entity Type

Home Improvement

Contact Information for Business Card

Company name: Brisk Fixwell
Name: Faridoullan Mestor
Position: Director
Ph:07952338417
Web: www.brisk-fixwell.com
Add: 42 Corvale Road
Hounslow
TW3 9KD
SECOND PERSON
Nizamuddel mestor
Position: Handyman
Ph: 07812 564037
Email: info@brisk-fixwell.com
Add: 18 Brackwin Lane Road
Hounslow
TW6 2LB

```html
<!DOCTYPE html>
<html lang="en">
<head>
<meta charset="utf-8">
<title>Brisk Fixwell Business Card</title>
<link rel="stylesheet" href="https://fonts.googleapis.com/css2?family=Roboto:wght@400;500;700&family=Rajdhani:wght@700&display=swap">
<style>
  :root {
    --navy: #22245e;
    --navy-soft: #3a3d7c;
    --red: #b91e1e;
    --white: #ffffff;
    --card-light: #f3f3f3;
    --ink: #2b2b2b;
    --backdrop: #b7b7b7;
  }
  * { margin: 0; padding: 0; box-sizing: border-box; }
  html, body {
    width: 1200px; height: 576px; overflow: hidden;
    background: var(--backdrop);
    font-family: "Roboto", Arial, sans-serif;
  }
  .canvas { position: relative; width: 1200px; height: 576px; }
  .card {
    position: absolute; top: 138px;
    width: 484px; height: 294px;
    border-radius: 12px; overflow: hidden;
  }

  /* Back side: services */
  .card-back { left: 82px; background: var(--navy); }
  .back-mark {
    position: absolute; top: 100px; left: 0; right: 0;
    text-align: center;
    font-weight: 700; font-size: 30px; letter-spacing: 1px;
    color: var(--navy-soft);
  }
  .services-band {
    position: absolute; left: 0; right: 0; bottom: 0; height: 46px;
    background: var(--red); color: var(--white);
    font-size: 13px; line-height: 16px; text-align: center;
    padding-top: 7px;
  }

  /* Front side: contact */
  .card-front { left: 602px; background: var(--card-light); }
  .brand {
    position: absolute; left: 38px; top: 126px;
    display: flex; align-items: center; gap: 10px;
  }
  .brand-name { font-weight: 700; font-size: 24px; color: var(--navy); }
  .brand-square { width: 22px; height: 22px; background: var(--red); }
  .person { position: absolute; left: 274px; top: 80px; }
  .person-name {
    font-family: "Rajdhani", "Roboto", sans-serif;
    font-weight: 700; font-size: 21px; color: var(--navy);
  }
  .person-role { font-size: 12.5px; color: var(--ink); margin-top: 1px; }
  .contact-list { position: absolute; left: 274px; top: 142px; list-style: none; }
  .contact-item {
    display: flex; align-items: center; gap: 10px;
    font-size: 13px; color: var(--ink); height: 18.5px;
  }
  .contact-icon { width: 11px; height: 11px; flex: none; }
  .front-bands { position: absolute; left: 0; bottom: 0; width: 484px; height: 42px; }
  .tagline {
    position: absolute; left: 274px; bottom: 11px;
    font-size: 12.5px; color: var(--white);
  }
</style>
</head>
<body>
<main class="canvas">

  <section class="card card-back" aria-label="Card back with services">
    <div class="back-mark">Brisk Fixwell</div>
    <div class="services-band">
      Electrical &nbsp;|&nbsp; Carpentry &nbsp;|&nbsp; Plumbing &nbsp;|&nbsp; Plastering &nbsp;|&nbsp; Flooring<br>
      Fencing &nbsp;|&nbsp; Decking &nbsp;|&nbsp; Painting &amp; Decorating
    </div>
  </section>

  <section class="card card-front" aria-label="Card front with contact details">
    <div class="brand">
      <span class="brand-name">Brisk Fixwell</span>
      <span class="brand-square"></span>
    </div>

    <div class="person">
      <div class="person-name">Faridoullan Mestor</div>
      <div class="person-role">Managing Director</div>
    </div>

    <ul class="contact-list">
      <li class="contact-item">
        <svg class="contact-icon" viewBox="0 0 12 12" aria-hidden="true">
          <path d="M1 4 Q6 0 11 4 L9 5 L8 3.5 L4 3.5 L3 5 Z" fill="var(--red)"/>
          <rect x="2.5" y="5.5" width="7" height="5" rx="1" fill="var(--red)"/>
        </svg>
        07952338417
      </li>
      <li class="contact-item">
        <svg class="contact-icon" viewBox="0 0 12 12" aria-hidden="true">
          <rect x="0.5" y="2.5" width="11" height="7" fill="var(--red)"/>
          <path d="M0.5 2.5 L6 7 L11.5 2.5" fill="none" stroke="var(--white)" stroke-width="1"/>
        </svg>
        info@brisk-fixwell.com
      </li>
      <li class="contact-item">
        <svg class="contact-icon" viewBox="0 0 12 12" aria-hidden="true">
          <circle cx="6" cy="6" r="5" fill="var(--red)"/>
          <path d="M1 6 H11 M6 1 V11 M6 1 Q3 6 6 11 M6 1 Q9 6 6 11" fill="none" stroke="var(--white)" stroke-width="0.7"/>
        </svg>
        www.brisk-fixwell.com
      </li>
    </ul>

    <svg class="front-bands" viewBox="0 0 484 42" aria-hidden="true">
      <rect x="0" y="31" width="220" height="11" fill="var(--red)"/>
      <path d="M214 0 H484 V42 H194 Z" fill="var(--navy)"/>
    </svg>
    <div class="tagline">Guarantee Arrival on Time</div>
  </section>

</main>
</body>
</html>
```